Corvane Freight online presence/customer portal track shipping

I sleek design showing what we do, broker freight. What we specialize in, chemicals and any freight where domestic or international. We want a home page, a customer portal button on front page that lets clients check on status of their freight (integrate with our transportation management system. Contact page,
COMPANIES THAT HAVE PALLETS TO MOVE.
https://www.tallowmerelogistics.com/
https://www.quivendale.com/
https://www.rkpellow.com/
3 page

```html
<!DOCTYPE html>
<html lang="en">
<head>
<meta charset="utf-8">
<title>Corvane Logistics — Home</title>
<link href="https://fonts.googleapis.com/css2?family=Poppins:wght@400;500;600;700;800&family=Open+Sans:wght@400;600;700&display=swap" rel="stylesheet">
<style>
:root{
  --brand-blue:#1f4f9e;
  --band-blue:#3476b9;
  --accent-red:#ef4b4f;
  --teal:#31b9a3;
  --ink:#222222;
  --muted:#444444;
  --mist:#f5f3f3;
  --footer:#2b2a2c;
  --white:#ffffff;
  --icon-blue:#2a6ab3;
}
*{margin:0;padding:0;box-sizing:border-box}
html,body{width:1200px;height:4470px;overflow:hidden;background:var(--white)}
body{font-family:"Open Sans",Arial,sans-serif;color:var(--ink)}
.page{position:relative;width:1200px;height:4470px;overflow:hidden}
.abs{position:absolute}
.btn{position:absolute;display:flex;align-items:center;justify-content:center;background:var(--accent-red);color:var(--white);font-family:"Poppins",sans-serif;font-weight:600;text-transform:uppercase;border-radius:6px;letter-spacing:.5px}
h1,h2,h3,h4{font-family:"Poppins",sans-serif}

/* hero */
.hero{position:absolute;left:0;top:0;width:1200px;height:603px;background:linear-gradient(100deg,#cfe2f1 0%,#9fc3e2 30%,#7a9a8c 55%,#4d6a74 75%,#9eb7c8 100%)}
.brand{position:absolute;left:48px;top:22px;display:flex;align-items:center;gap:12px}
.brand-dot{width:46px;height:46px;border-radius:50%;background:var(--brand-blue)}
.brand-name{font-family:"Poppins",sans-serif;font-weight:600;font-size:26px;color:var(--brand-blue)}
.nav{position:absolute;left:470px;top:30px;display:flex;align-items:center}
.nav a{font-family:"Poppins",sans-serif;font-weight:600;font-size:15px;color:var(--white);text-decoration:none;padding:6px 12px;margin-right:12px}
.nav a.active{background:var(--accent-red)}
.portal{position:absolute;left:1009px;top:25px;width:168px;height:36px;border:2px solid var(--white);border-radius:8px;color:var(--white);font-family:"Poppins",sans-serif;font-weight:600;font-size:14px;display:flex;align-items:center;justify-content:center}
.hero-title{position:absolute;left:120px;top:222px;font-weight:700;font-size:38px;line-height:56px;color:var(--brand-blue)}
.dots{position:absolute;left:562px;top:558px;display:flex;gap:9px;align-items:center}
.dots span{width:7px;height:7px;border-radius:50%;background:var(--white)}
.dots span.on{width:12px;height:12px;border:3px solid var(--accent-red)}

/* welcome */
.welcome{position:absolute;left:0;top:603px;width:1200px;height:495px;background:var(--band-blue);color:var(--white)}
.welcome .kicker{position:absolute;left:132px;top:60px;font-family:"Poppins",sans-serif;font-weight:500;font-size:19px}
.welcome h2{position:absolute;left:132px;top:88px;font-weight:600;font-size:32px}
.welcome h2 .cap{font-size:56px;line-height:1}
.welcome p{position:absolute;left:132px;top:187px;width:340px;font-size:14.5px;line-height:22.5px}
.welcome .photo{position:absolute;left:534px;top:58px;width:536px;height:381px;background:linear-gradient(180deg,#8ea5c9 0%,#a9bbd6 50%,#6f86ad 100%)}

/* services card */
.port{position:absolute;left:0;top:1098px;width:1200px;height:369px;background:linear-gradient(100deg,#3e4a5a 0%,#8a6a52 45%,#e0924a 80%,#f4c57a 100%)}
.mist{position:absolute;left:0;top:1467px;width:1200px;height:990px;background:var(--mist)}
.card{position:absolute;left:132px;top:1271px;width:938px;height:555px;background:var(--white);box-shadow:0 4px 14px rgba(0,0,0,.12);text-align:center}
.card h2{position:absolute;left:0;right:0;top:36px;font-weight:600;font-size:26px;color:var(--ink)}
.card .lead{position:absolute;left:150px;right:150px;top:98px;font-size:12.5px;line-height:20px;color:var(--muted)}
.svc{position:absolute;top:190px;width:234px;height:195px}
.svc+.svc{border-left:1px solid #e1e1e1}
.svc svg{display:block;margin:12px auto 0}
.svc h3{margin-top:30px;font-weight:500;font-size:15px;color:var(--ink)}
.svc p{margin:10px auto 0;width:170px;font-size:12.5px;line-height:18px;color:var(--muted)}

/* specialize */
.section-title{position:absolute;left:0;right:0;text-align:center;font-family:"Poppins",sans-serif;font-weight:600;font-size:26px;color:var(--ink)}
.section-sub{position:absolute;left:0;right:0;text-align:center;font-size:13px;color:var(--ink)}
.spec-icon{position:absolute;width:76px;height:76px;border-radius:18px;background:var(--icon-blue);display:flex;align-items:center;justify-content:center}
.spec h4{font-weight:600;font-size:15px;color:var(--ink)}
.spec p{margin-top:8px;font-size:12.5px;line-height:18px;color:var(--muted)}
.spec{position:absolute}
.ship-photo{position:absolute;left:408px;top:2162px;width:384px;height:384px;border-radius:50%;background:linear-gradient(180deg,#cfe1f0 0%,#b4c9dc 40%,#c8643a 62%,#2a4f8f 78%,#3a6db3 100%)}

/* what we do */
.tile{position:absolute;width:300px;height:220px}
.tile-label{position:absolute;width:300px;text-align:center;font-family:"Poppins",sans-serif;font-weight:600;font-size:18px;color:var(--ink)}

/* blog */
.blog{position:absolute;left:0;top:3218px;width:1200px;height:552px;background:var(--band-blue);color:var(--white)}
.blog h2{position:absolute;left:0;right:0;top:48px;text-align:center;font-weight:500;font-size:26px}
.blog .rule{position:absolute;left:578px;top:101px;width:50px;height:3px;background:var(--white)}
.post{position:absolute;top:160px;width:292px;height:312px;border:2px solid var(--white)}
.post h3{position:absolute;left:26px;top:32px;width:262px;font-weight:600;font-size:17px;line-height:27px;letter-spacing:-.2px}
.post p{position:absolute;left:28px;top:146px;width:212px;font-size:12px;line-height:17.5px}
.post .btn{left:44px;top:297px;width:96px;height:32px;font-size:12px}

/* help */
.help{position:absolute;left:0;top:3770px;width:1200px;height:357px;background:var(--teal);color:var(--white);text-align:center}
.help h2{position:absolute;left:0;right:0;top:62px;font-weight:800;font-size:32px}
.help p{position:absolute;left:270px;right:270px;top:132px;font-size:19px;line-height:29px}

/* footer */
.footer{position:absolute;left:0;top:4127px;width:1200px;height:343px;background:var(--footer);color:var(--white)}
.footer-brand{position:absolute;left:139px;top:98px;display:flex;align-items:center;gap:14px}
.footer-brand .brand-dot{width:64px;height:64px;background:#c93a3f}
.footer-brand span{font-family:"Poppins",sans-serif;font-weight:600;font-size:23px}
.f-head{position:absolute;top:44px;font-family:"Poppins",sans-serif;font-weight:600;font-size:13px}
.f-menu{position:absolute;left:486px;top:82px;font-size:12px;line-height:20px;text-transform:uppercase}
.f-row{position:absolute;display:flex;gap:12px;align-items:flex-start;font-size:12px;line-height:16px}
.f-ic{width:24px;height:24px;border-radius:50%;background:var(--white);flex:none;display:flex;align-items:center;justify-content:center}
.f-rule{position:absolute;left:139px;top:260px;width:930px;height:1px;background:#4a494b}
.copy{position:absolute;left:0;right:0;top:301px;text-align:center;font-size:10px}
</style>
</head>
<body>
<div class="page">

  <header class="hero" role="img" aria-label="Photo of a white semi-truck driving on a mountain road at sunrise">
    <div class="brand"><div class="brand-dot"></div><span class="brand-name">Corvane Logistics</span></div>
    <nav class="nav">
      <a class="active">HOME</a><a>ABOUT US</a><a>SERVICES</a><a>CAREERS</a><a>CONTACT US</a>
    </nav>
    <div class="portal">CUSTOMER PORTAL</div>
    <h1 class="hero-title">Accurately Promising,<br>Reliably Delivering</h1>
    <div class="btn" style="left:121px;top:364px;width:151px;height:47px;font-size:16px">Get Started</div>
    <div class="dots"><span></span><span></span><span class="on"></span><span></span><span></span></div>
  </header>

  <section class="welcome">
    <div class="kicker">Welcome to</div>
    <h2><span class="cap">C</span>orvane Logistics</h2>
    <p>There are many variations of passages of Lorem Ipsum available, but the majority have suffered alteration in some form, by injected humour, or randomised words which don't look even slightly believable. If you are going to use a passage of Lorem Ipsum, you need to be sure there isn't anything embarrassing hidden in the middle of text.</p>
    <div class="btn" style="left:134px;top:396px;width:107px;height:34px;font-size:13px">Read More</div>
    <div class="photo" role="img" aria-label="Photo of a cargo airplane taking off over a runway"></div>
  </section>

  <div class="port" role="img" aria-label="Photo of a container port with cranes at sunset"></div>
  <div class="mist"></div>

  <section class="card">
    <h2>Global Integrated Logistics</h2>
    <p class="lead">Corvane Logistics specializes in moving regulated and non-regulated chemical freight of all kinds Operating in 49 states and Canada Corvane Logistics' focus is in brokering van or flatbed, tanker endorsed, liquid bulk, drayage, intermodal, and international chemical shipments of all combinations.</p>
    <div class="svc" style="left:0">
      <svg width="100" height="64" viewBox="0 0 100 64" fill="none" stroke="#2a6ab3" stroke-width="2.5" stroke-linejoin="round"><path d="M8 44 L88 14 Q96 12 94 20 L20 50 Z"/><path d="M44 30 L30 6 L40 4 L62 24"/><path d="M50 36 L56 58 L64 56 L66 30"/><path d="M12 40 L6 28 L14 26 L22 36"/></svg>
      <h3>Air Freight</h3><p>There are many variations of passages of Lorem Ipsum available, but the majority have suffered alter.</p>
    </div>
    <div class="svc" style="left:234px">
      <svg width="100" height="64" viewBox="0 0 100 64" fill="none" stroke="#2a6ab3" stroke-width="2.5" stroke-linejoin="round"><path d="M6 40 H94 L86 58 H14 Z"/><rect x="14" y="26" width="54" height="14"/><rect x="70" y="12" width="16" height="28"/><path d="M28 26 V40 M42 26 V40 M56 26 V40"/></svg>
      <h3>Ocean Freight</h3><p>There are many variations of passages of Lorem Ipsum available, but the majority have suffered alter.</p>
    </div>
    <div class="svc" style="left:468px">
      <svg width="110" height="64" viewBox="0 0 110 64" fill="none" stroke="#2a6ab3" stroke-width="2.5" stroke-linejoin="round"><rect x="4" y="10" width="68" height="38"/><path d="M76 20 H94 L104 34 V48 H76 Z"/><circle cx="22" cy="54" r="5"/><circle cx="36" cy="54" r="5"/><circle cx="90" cy="54" r="5"/></svg>
      <h3>Road Freight</h3><p>There are many variations of passages of Lorem Ipsum available, but the majority have suffered alter.</p>
    </div>
    <div class="svc" style="left:702px">
      <svg width="100" height="64" viewBox="0 0 100 64" fill="none" stroke="#2a6ab3" stroke-width="2.5" stroke-linejoin="round"><path d="M28 2 H62 L72 12 V62 H28 Z"/><path d="M36 18 H58 M36 28 H64 M36 38 H64 M36 48 H52"/><path d="M60 50 L80 20 L86 24 L66 54 L58 56 Z"/></svg>
      <h3>Contract Logistics</h3><p>There are many variations of passages of Lorem Ipsum available, but the majority have suffered alter.</p>
    </div>
    <div class="btn" style="left:386px;top:474px;width:162px;height:36px;font-size:13px">View All Services</div>
  </section>

  <h2 class="section-title" style="top:1898px">We Specialize In</h2>
  <p class="section-sub" style="top:1956px">There are many variations of passages of Lorem Ipsum available lorem ipsum</p>

  <svg class="abs" style="left:270px;top:2075px" width="660" height="150" viewBox="0 0 660 150" fill="none" stroke="#d6d3d3" stroke-width="1"><path d="M4 4 L150 142"/><path d="M652 4 L510 142"/></svg>

  <div class="ship-photo" role="img" aria-label="Photo of a container ship loaded with cargo at a port"></div>
  <div class="abs" style="left:0;top:2457px;width:1200px;height:100px;background:var(--white)"></div>

  <div class="spec-icon" style="left:484px;top:2050px"><svg width="44" height="44" viewBox="0 0 44 44" fill="none" stroke="#fff" stroke-width="3"><circle cx="16" cy="28" r="12"/><path d="M24 20 L38 6"/><circle cx="12" cy="30" r="2" fill="#fff"/><circle cx="20" cy="30" r="2" fill="#fff"/></svg></div>
  <div class="spec" style="left:581px;top:2052px;width:200px"><h4>Chemicals</h4><p>Corrosive 8 and Flammable<br>3 class chemicals</p></div>

  <div class="spec-icon" style="left:135px;top:2245px"><svg width="48" height="36" viewBox="0 0 48 36" fill="#fff"><path d="M2 20 H46 L40 32 H8 Z"/><rect x="10" y="10" width="22" height="8"/><rect x="34" y="4" width="6" height="14"/></svg></div>
  <div class="spec" style="left:227px;top:2238px;width:170px"><h4>Drayage</h4><p>Whether Sea or Rail Port Corvane Logistics has relationships that prove to avoid demurrage and move your freight to it's final destination.</p></div>

  <div class="spec-icon" style="left:815px;top:2245px"><svg width="46" height="34" viewBox="0 0 46 34" fill="none" stroke="#fff" stroke-width="2.5"><rect x="2" y="2" width="42" height="30"/><path d="M10 2 V32 M18 2 V32 M26 2 V32 M34 2 V32"/></svg></div>
  <div class="spec" style="left:912px;top:2242px;width:150px"><h4>LTL</h4><p>Having negotiated rates with over 120 LTL carriers give any shipper their choice in moving their cargo.</p></div>

  <h2 class="section-title" style="top:2506px">What We Do</h2>
  <p class="section-sub" style="top:2552px">There are many variations of passages of Lorem Ipsum available lorem ipsum</p>

  <div class="tile" style="left:134px;top:2608px;background:linear-gradient(160deg,#9a9a95,#c9c6c0 60%,#7d7a72)" role="img" aria-label="Photo of a storm drain grate on gravel"></div>
  <div class="tile" style="left:451px;top:2608px;background:linear-gradient(180deg,#aac6e4 0%,#b99a86 55%,#c7b299 100%)" role="img" aria-label="Photo of a white passenger van in a desert valley"></div>
  <div class="tile" style="left:768px;top:2608px;background:linear-gradient(135deg,#d9d9d9,#8d8d8d 50%,#e6c23a 85%)" role="img" aria-label="Photo of a car wheel on a flatbed trailer"></div>
  <p class="tile-label" style="left:134px;top:2846px">Drayage</p>
  <p class="tile-label" style="left:451px;top:2846px">Dry Van</p>
  <p class="tile-label" style="left:768px;top:2846px">Flatbed</p>

  <div class="tile" style="left:134px;top:2897px;background:linear-gradient(180deg,#b8d0e8 0%,#8fae72 50%,#5e8a3a 100%)" role="img" aria-label="Photo of a tanker truck on a green countryside road"></div>
  <div class="tile" style="left:451px;top:2897px;background:linear-gradient(180deg,#f2f2f2,#d4d6d8 70%,#6d6e70)" role="img" aria-label="Photo of a refrigerated white trailer"></div>
  <div class="tile" style="left:768px;top:2897px;background:linear-gradient(120deg,#3a2b24,#6b4a3a 50%,#c45a3a 80%,#e8b76a)" role="img" aria-label="Photo of a box truck on a road at dusk"></div>
  <p class="tile-label" style="left:134px;top:3134px">Liquid Bulk</p>
  <p class="tile-label" style="left:451px;top:3134px">Reefer</p>
  <p class="tile-label" style="left:768px;top:3134px">Hot Shot/Box Trucks</p>

  <section class="blog">
    <h2>Latest Blog</h2>
    <div class="rule"></div>
    <article class="post" style="left:140px">
      <h3>Lorem Ipsum is simply<br>dummy text of the printing<br>and typesetting industry</h3>
      <p>Sed ut perspiciatis unde omnis iste natus error sit voluptatem accusantium doloremque laudantium, totam rem aperiam, eaque ipsa quae ab illo inventore veritatis et quasi architecto beatae vitae dicta s</p>
      <div class="btn">Read More</div>
    </article>
    <article class="post" style="left:461px">
      <h3>Lorem Ipsum is simply<br>dummy text of the printing<br>and typesetting industry</h3>
      <p>Sed ut perspiciatis unde omnis iste natus error sit voluptatem accusantium doloremque laudantium, totam rem aperiam, eaque ipsa quae ab illo inventore veritatis et quasi architecto beatae vitae dicta s</p>
      <div class="btn">Read More</div>
    </article>
    <article class="post" style="left:782px">
      <h3>Lorem Ipsum is simply<br>dummy text of the printing<br>and typesetting industry</h3>
      <p>Sed ut perspiciatis unde omnis iste natus error sit voluptatem accusantium doloremque laudantium, totam rem aperiam, eaque ipsa quae ab illo inventore veritatis et quasi architecto beatae vitae dicta s</p>
      <div class="btn">Read More</div>
    </article>
  </section>

  <section class="help">
    <h2>HOW CAN WE HELP YOU?</h2>
    <p>At vero eos et accusamus et iusto odio dignissimos ducimus qui blanditiis praesentium voluptatum deleniti atque corrupti quos dolores et quas molestias excepturi sint occaecati cupiditate non provident,</p>
    <div class="btn" style="left:520px;top:258px;width:137px;height:40px;font-size:13px">Contact Us</div>
  </section>

  <footer class="footer">
    <div class="footer-brand"><div class="brand-dot"></div><span>Corvane Freight</span></div>
    <div class="f-head" style="left:486px">MENU</div>
    <div class="f-menu">Home<br>About Us<br>Services<br>Careers<br>Contact Us</div>
    <div class="f-head" style="left:676px">CONTACT US</div>
    <div class="f-row" style="left:676px;top:82px"><span class="f-ic"><svg width="10" height="14" viewBox="0 0 10 14" fill="#2b2a2c"><path d="M5 0 A5 5 0 0 1 10 5 C10 9 5 14 5 14 C5 14 0 9 0 5 A5 5 0 0 1 5 0 Z"/><circle cx="5" cy="5" r="2" fill="#fff"/></svg></span><span>2716 Harlow Street<br>Brenmoor, CA 90482</span></div>
    <div class="f-row" style="left:676px;top:132px"><span class="f-ic"><svg width="12" height="12" viewBox="0 0 12 12" fill="#2b2a2c"><path d="M2 0 L5 3 L3.5 5 Q5 8 7 8.5 L9 7 L12 10 L10 12 Q3 11 0 2 Z"/></svg></span><span>Call Us<br>555.014.2290</span></div>
    <div class="f-row" style="left:676px;top:182px"><span class="f-ic"><svg width="13" height="10" viewBox="0 0 13 10" fill="none" stroke="#2b2a2c" stroke-width="1.5"><rect x="1" y="1" width="11" height="8"/><path d="M1 1 L6.5 5.5 L12 1"/></svg></span><span>E mail Us<br>info@corvanefreight.com</span></div>
    <div class="f-head" style="left:968px">FOLLOW US</div>
    <div class="f-row" style="left:968px;top:82px"><span class="f-ic"></span><span>Like us on<br>PAGECAST</span></div>
    <div class="f-row" style="left:968px;top:132px"><span class="f-ic"></span><span>Follow us on<br>CHIRPLINE</span></div>
    <div class="f-row" style="left:968px;top:182px"><span class="f-ic"></span><span>Follow us on<br>WORKGRID</span></div>
    <div class="f-rule"></div>
    <p class="copy">Copyright © 2021 All Rights Reserved</p>
  </footer>

</div>
</body>
</html>
```